VC Liquidity Transformation Case Study Design

2-Page VC Case Study Brochure Concept
We are looking for visual design concepts, not finished production files.
This project explores a 2-page institutional brochure for Brisket Partners that:
Page 1 → Explains our differentiated approach to venture-backed technology exits
Page 2 → Demonstrates how we convert long-tenured portfolio companies into strategic outcomes
The attached Design Guide includes:
• Page wireframe
• Referenced visuals
• Icon direction
• Tone and design rules
Designers should use this as a structural guide, not a constraint.

- BP Process Diagram: several modifications needed to the images to be recreated (various images attached)
- Brisket Partners 2-Page Brochure small (B1 and Final F1 - psd files) are my current 2 page brochure. Leverage if you'd like.
- Logo package: this is the package of Brisket Partners logos

Target Market(s)

Institutional capital investors like Venture capitalists and private equity groups

Industry/Entity Type

investment banking

Font styles to use
Sans Serif

Colors
0054AA
0677BA
7BADD7
CADEEF
E8F1F8

Requirements
Must have
• See design guide
Nice to have
• See design guide
Should not have
• See design guide

```html
<!DOCTYPE html>
<html lang="en">
<head>
<meta charset="utf-8">
<title>Brisket Partners – Two-Page Brochure</title>
<link href="https://fonts.googleapis.com/css2?family=Cinzel:wght@400;600&family=Montserrat:ital,wght@0,400;0,500;0,600;0,700;1,400&display=swap" rel="stylesheet">
<style>
:root{
  --navy:#1d3f87;
  --blue:#0054AA;
  --teal:#0677BA;
  --sky:#7BADD7;
  --mist:#CADEEF;
  --ice:#E8F1F8;
  --ink:#14213d;
  --bg:#dedfe1;
  --serif:'Cinzel',serif;
  --sans:'Montserrat',sans-serif;
}
*{margin:0;padding:0;box-sizing:border-box}
html,body{width:753px;height:1200px;overflow:hidden;background:var(--bg)}
body{font-family:var(--sans);color:var(--ink);position:relative}
.page{position:absolute;left:151px;width:450px;height:582px;background:#fff;overflow:hidden;box-shadow:0 2px 6px rgba(0,0,0,.12)}
.page-one{top:12px}
.page-two{top:606px}
.abs{position:absolute}
.caps{font-family:var(--serif);text-transform:uppercase;letter-spacing:.02em}

/* page one */
.hero{left:0;top:0;width:450px;height:211px;background:linear-gradient(100deg,#0d3f86 0%,#1d5fa0 45%,#7ea9cf 78%,#c8dcee 100%)}
.brand{left:19px;top:18px;color:#fff;display:flex;align-items:center;gap:6px}
.brand-dot{width:14px;height:14px;border-radius:50%;background:#fff}
.brand-name{font-family:var(--serif);font-size:12px;line-height:1.05;letter-spacing:.08em}
.hero-title{left:19px;top:92px;color:#fff;font-size:16.5px;line-height:1.25}
.hero-copy{left:19px;top:141px;width:280px;color:#fff;font-size:6.2px;line-height:1.45}
.hero-copy p{margin-bottom:6px}
.reality-title{left:19px;top:220px;color:var(--blue);font-size:16px;line-height:1.25}
.reality-sub{left:19px;top:268px;color:var(--teal);font-size:6.5px}
.reality-list{left:19px;top:285px;list-style:none;font-size:9.2px;font-weight:500;line-height:1.6}
.reality-graphic{left:183px;top:203px;width:252px;height:143px;border-radius:6px;background:#fff;box-shadow:0 1px 5px rgba(0,0,0,.15)}
.reality-graphic .art{position:absolute;left:8px;top:10px;width:236px;height:112px;border-radius:4px;background:linear-gradient(90deg,var(--ice),#f7f9fc 50%,#fbf6e6)}
.reality-graphic .cap{position:absolute;left:0;right:0;bottom:6px;text-align:center;font-size:5.5px;font-style:italic;color:#555}
.backlog{left:11px;top:351px;width:427px;height:222px;border-radius:8px;background:linear-gradient(135deg,var(--navy),var(--teal));color:#fff}
.backlog-title{left:0;right:0;top:12px;text-align:center;font-size:15px}
.backlog-sub{left:0;right:0;top:29px;text-align:center;font-size:5.6px}
.stat-pill{left:16px;top:41px;width:394px;height:17px;border:1px solid #fff;border-radius:9px;display:flex}
.stat-pill span{flex:1;text-align:center;font-family:var(--serif);font-size:11px;line-height:15px}
.stat-labels{left:16px;top:64px;width:394px;display:flex}
.stat-labels span{flex:1;text-align:center;font-size:6.2px;line-height:1.3}
.backlog-copy{left:20px;top:101px;width:386px;text-align:center;font-size:5.8px;line-height:1.4}
.backlog-result{left:20px;top:127px;width:386px;text-align:center;font-size:5.8px}
.lifecycle-title{left:19px;top:164px;font-size:16px;line-height:1.4}
.lifecycle-icons{left:136px;top:149px}
.lifecycle-bar{left:136px;top:175px}
.lifecycle-notes{left:147px;top:199px;display:flex;align-items:flex-start;gap:14px}
.note-label{font-size:9.5px;font-weight:600}
.note-engage{font-size:6.8px;font-weight:600;line-height:1.1}
.note-engage small{display:block;font-size:3.8px;font-weight:400}
.note-list{font-size:3.8px;line-height:1.3;list-style:none}

/* page two */
.spread-title{left:0;right:0;top:20px;text-align:center;color:var(--blue);font-size:18px;line-height:1.18}
.spread-sub{left:0;right:0;top:75px;text-align:center;font-size:10px;font-weight:700}
.col{top:92px;width:135px;height:158px;border-radius:7px;background:var(--navy);overflow:hidden}
.col-head{margin:4px;height:36px;border-radius:5px;background:#fff;color:var(--blue);display:flex;align-items:center;justify-content:center;text-align:center;font-size:10.5px;line-height:1.1}
.col ul{list-style:none;color:#fff;font-size:5.8px;line-height:1.3;padding:6px 10px 0 14px}
.col li{margin-bottom:8px;text-indent:-4px}
.col li::before{content:"• "}
.col-mid{background:#fff;box-shadow:0 1px 4px rgba(0,0,0,.18)}
.col-mid .col-head{background:var(--teal);color:#fff;height:56px;flex-direction:column;font-size:10.5px}
.col-mid .col-head small{font-size:6px;margin-bottom:3px}
.col-mid ul{color:var(--ink);padding-top:4px}
.col-mid li{margin-bottom:5px}
.col-mid .note{color:var(--blue);font-size:6px;font-weight:700;text-align:center;padding:0 8px;line-height:1.3}
.transform-panel{left:0;top:258px;width:450px;height:324px;border-radius:10px 10px 0 0;background:linear-gradient(135deg,var(--navy),var(--teal))}
.card{left:26px;width:397px;border-radius:8px;background:#fff}
.card-top{top:9px;height:128px}
.card-bottom{top:144px;height:131px}
.transform-title{left:17px;top:18px;color:var(--blue);font-size:14px;line-height:1.3}
.transform-list{left:17px;top:62px;list-style:none;font-size:8.8px;font-weight:600;line-height:1.5}
.transform-art{left:195px;top:16px;width:196px;height:106px;border-radius:4px;background:linear-gradient(90deg,var(--ice),#fff 50%,var(--ice))}
.outcome-label{left:60px;top:9px;width:100px;text-align:center;font-size:5.8px;color:#444}
.outcome-icons{left:12px;top:38px;display:flex;gap:9px}
.outcome-icon{width:38px;text-align:center;font-size:4.8px;color:#444;line-height:1.3}
.outcome-icon i{display:block;margin:0 auto 5px;width:22px;height:22px;border-radius:50%;background:radial-gradient(circle,var(--mist),var(--ice))}
.outcome-cap{left:0;width:250px;top:120px;text-align:center;font-size:4.8px;font-style:italic;color:#666}
.outcomes-title{left:227px;top:18px;color:var(--blue);font-size:14px}
.outcomes-list{left:227px;top:37px;list-style:none;font-size:9.2px;font-weight:600;line-height:1.35}
.outcomes-list li{margin-bottom:2px}
.tagline{left:0;right:0;top:543px;text-align:center;color:#fff;font-size:6.4px;font-weight:700}
.contact{left:20px;top:553px;width:410px;height:16px;border-radius:8px;background:#fff;text-align:center;font-size:6px;line-height:16px;color:var(--blue)}
</style>
</head>
<body>

<section class="page page-one">
  <div class="abs hero" role="img" aria-label="Photograph of a steel arch bridge fading into blue mist"></div>
  <div class="abs brand"><span class="brand-dot"></span><span class="brand-name">BRISKET<br>PARTNERS</span></div>
  <h1 class="abs hero-title caps">The Overlooked Majority<br>in Venture Portfolios</h1>
  <div class="abs hero-copy">
    <p>Most venture portfolios contain a small number of unicorns and a much larger set of technically strong companies that plateau before liquidity.</p>
    <p>These companies often hold valuable IP, but lack a clear strategic exit pathway.</p>
    <p>Brisket Partners helps Venture Investors Transition Long Tenured Portfolio Companies Into Strategic Outcomes</p>
  </div>

  <h2 class="abs reality-title caps">Portfolio<br>Reality Graphic</h2>
  <div class="abs reality-sub">Typical VC Portfolio</div>
  <ul class="abs reality-list">
    <li>• 2 Unicorns</li>
    <li>• 3 Failures</li>
    <li>• 5 Long-Tenured Companies</li>
  </ul>
  <div class="abs reality-graphic">
    <div class="art" role="img" aria-label="Illustration comparing traditional focus on unicorns and losses with a focus on long-tenured companies through a technology lens"></div>
    <div class="cap">Unlocking value from the overlooked majority</div>
  </div>

  <div class="abs backlog">
    <h2 class="abs backlog-title caps">The Venture Exit Backlog</h2>
    <p class="abs backlog-sub">Extended holding periods, peak valuation vintages, and limited IPO pathways are creating a growing backlog of venture exits.</p>
    <div class="abs stat-pill"><span>6.0 YRS</span><span>2021–2022</span><span>50%</span><span>45 IPOS</span><span>10 + 2</span></div>
    <div class="abs stat-labels">
      <span>Median Venture Hold Duration Peak Valuation Vintages</span>
      <span>Peak Valuation Vintages</span>
      <span>Pre-Pandemic Portfolio Inventory</span>
      <span>Tech IPO Window</span>
      <span>10, 2 + Continuation Vehicle Extended Fund Duration</span>
    </div>
    <p class="abs backlog-copy">Longer hold periods, peak valuation vintages, and limited IPO access have created a growing population of long-tenured venture portfolio companies awaiting liquidity.</p>
    <p class="abs backlog-result"><b>Result:</b> Venture portfolios contain a growing backlog of companies with valuable technology but unclear exit pathways.</p>
    <h2 class="abs lifecycle-title caps">Venture<br>Lifecycle</h2>
    <svg class="abs lifecycle-icons" width="280" height="26" viewBox="0 0 280 26" fill="none" stroke="#fff" stroke-width="1.2">
      <path d="M20 20h12M22 18v-5M26 18v-8M30 18v-11"/>
      <circle cx="70" cy="9" r="4"/><circle cx="77" cy="16" r="3"/>
      <path d="M120 22c20-6 60-12 155-18" stroke-width=".7"/>
      <circle cx="130" cy="13" r="6"/><path d="M130 10v4M130 16v1"/>
      <circle cx="190" cy="13" r="6"/><circle cx="190" cy="13" r="2.5"/>
      <path d="M240 8v9M244 7v10M238 17c2 3 6 3 8 0"/>
    </svg>
    <svg class="abs lifecycle-bar" width="282" height="14" viewBox="0 0 282 14" font-family="Montserrat,sans-serif" font-size="5.6" fill="#fff">
      <g stroke="#fff" stroke-width=".8">
        <polygon points="1,1 52,1 57,7 52,13 1,13" fill="none"/>
        <polygon points="55,1 100,1 105,7 100,13 55,13 60,7" fill="#7BADD7"/>
        <polygon points="103,1 145,1 150,7 145,13 103,13 108,7" fill="none"/>
        <polygon points="148,1 220,1 225,7 220,13 148,13 153,7" fill="#4f8cc4"/>
        <polygon points="223,1 276,1 281,7 276,13 223,13 228,7" fill="none"/>
      </g>
      <text x="8" y="9">Early Growth</text>
      <text x="70" y="9">Scaling</text>
      <text x="116" y="9">Plateau</text>
      <text x="158" y="9">Strategic Transition</text>
      <text x="238" y="9">Liquidity</text>
    </svg>
    <div class="abs lifecycle-notes">
      <span class="note-label">Important Label</span>
      <span class="note-engage">Brisket Engages Here<small>The moment a company becomes:</small></span>
      <ul class="note-list"><li>• Technically Strong</li><li>• Strategically Misunderstood</li><li>• Capital Inefficient</li></ul>
    </div>
  </div>
</section>

<section class="page page-two">
  <h1 class="abs spread-title caps">From Long-Tenured Holding<br>to Strategic Outcome</h1>
  <p class="abs spread-sub">How Brisket enables venture capital recycling.</p>

  <div class="abs col" style="left:18px">
    <div class="col-head caps">The Challenge</div>
    <ul>
      <li>Technically strong platforms</li>
      <li>Limited growth trajectory</li>
      <li>Misunderstood strategic value</li>
      <li>Capital trapped in mature holdings</li>
    </ul>
  </div>
  <div class="abs col col-mid" style="left:158px">
    <div class="col-head caps"><small>Brisket Intervention<br>Vertical Framework</small>Core Asset<br>Pathway</div>
    <ul>
      <li>Strategic Reframing</li>
      <li>Buyer Mapping</li>
      <li>Multi-Rationale Positioning</li>
      <li>Global Strategic Process</li>
    </ul>
    <p class="note">Traditional processes focus on financial buyers and revenue multiples.</p>
  </div>
  <div class="abs col" style="left:296px">
    <div class="col-head caps">Process Outcome</div>
    <ul>
      <li>Cross-Sector Buyer Engagement</li>
      <li>Global Strategic Process</li>
      <li>Accelerated Closing</li>
      <li>Capability-Based Pricing</li>
    </ul>
  </div>

  <div class="abs transform-panel">
    <div class="abs card card-top">
      <h2 class="abs transform-title caps">Large Visual<br>Transformation.</h2>
      <ul class="abs transform-list">
        <li>• Plateaued Company</li>
        <li>• Brisket Engagement</li>
        <li>• Strategic Exit</li>
      </ul>
      <div class="abs transform-art" role="img" aria-label="Diagram of a plateaued company moving through Brisket engagement to strategic exits, with outcome icons"></div>
    </div>
    <div class="abs card card-bottom">
      <div class="abs outcome-label">Outcome</div>
      <div class="abs outcome-icons">
        <div class="outcome-icon"><i role="img" aria-label="Network icon"></i>Cross-Sector Buyer Engagement</div>
        <div class="outcome-icon"><i role="img" aria-label="Globe icon"></i>A Competitive &amp; Global Process</div>
        <div class="outcome-icon"><i role="img" aria-label="Clock icon"></i>Accelerated Closing<br>(2–4 mo post LOI)</div>
        <div class="outcome-icon"><i role="img" aria-label="Hand with coins icon"></i>Strategic Liquidity</div>
      </div>
      <div class="abs outcome-cap">Unlocking value from the overlooked majority</div>
      <h2 class="abs outcomes-title caps">Outcomes Row</h2>
      <ul class="abs outcomes-list">
        <li>• Capital Returned</li>
        <li>• Portfolio Refreshed</li>
        <li>• IP Value Unlocked</li>
        <li>• New Funds / Investments<br>&nbsp;&nbsp;Enabled</li>
      </ul>
    </div>
  </div>
  <p class="abs tagline">Aligning IP-rich companies with strategic demand unlocks liquidity where traditional exits stall.</p>
  <div class="abs contact">2180 Harbor View Parkway Suite 410, Austin TX 78701 &nbsp;|&nbsp; info@BrisketPartners.com &nbsp;|&nbsp; www.BrisketPartners.com</div>
</section>

</body>
</html>
```